Start up International Security Business Needs a Web Design

Based in Edinburgh UK, Morvane Global Services (www.morvanegs.example) provides security services of various types in challenging or high threat environments internationally for government and private sector organizations. We provide risk assessments, security audits and training, medical support, close protection for individuals, groups and events, crisis management, and evacuation coordination; we enable businesses to operate in challenging locations. Our experts are highly trained and qualified with exceptional experience worldwide.
The name Morvane was selected in competition and derives from Greek Mythology where it was a giant man of bronze gifted by Zeus to protect Europa from invaders and pirates, circling the island of Crete three times daily (essentially establishing a protective perimeter). The centre of the current logo (inside the "O") is a stylized symbol of Zeus; we use it as a customized "bullet" on documents and acts as an abbreviated logo.
We purposefully omitted any reference to security in the name/logo and the web-page should be discreet in the same manner - we provide services of this nature but do not draw attention to ourselves. Generic images for visuals should be used as opposed to any existing stock photography we possess as a company. Imagery that relay protection, an international reach, innovation, modern vistas, varied countrysides (desert, jungle, urban settings, an old fortress?) would be seen positively.
The current colour of blue and white in the principal logo has received positive response for the clean lines, and the grey-ish scale writing similarly works. The "O" with the symbol inside has been used as customized "bullets" inside of documents, and we envisioned several other potential uses for web pages, etc.
However the integration of bronze as a third colour given the origin of Morvane could be a consideration as well.
The final design should communicate clarity, an international reach in difficult areas with our broad experience and strength without being aggressive. There must be a section where the countries we have experience operating in is displayed graphically (i.e. a global map where the countries are coloured in). Countries are USA, Canada, UK, France, Bosnia, UAE, Qatar, Libya, Tunisia, Afghanistan, Iraq, Turkey, Sudan, Egypt, Central African Republic, Somalia, Rwanda, Somaliland. Additional sections should include "Our Clients", "Our Services", "Our Expertise", "Join Our Team" which should have a personal details form and ability to upload a CV, "Our Contact Details" which should also allow for submission of a web enquiry
Reason: Extension granted at the request of several designers in order to conceptualize solutions whilst initial selection process begins. Feedback on each design submitted will be provided. Very many thanks to all who took the time to share their vision for our company's website.
Morvane GS
Target Market(s)
Private Sector energy, logistics, and infrastructure companies along with government organizations
Industry/Entity Type
Security
Logo Text
Morvane
Number of Pages Required
3 page
Requirements
Must have
- There must be a section where the countries we have experience operating in is displayed graphically (i.e. a global map where the countries are coloured in). Countries are USA, Canada, UK, France, Bosnia, UAE, Qatar, Libya, Tunisia, Afghanistan, Iraq, Turkey, Sudan, Egypt, Central African Republic, Somalia, Rwanda, Somaliland. Additional sections should include "Our Clients", "Our Services", "Our Expertise", "Join Our Team" which should have a personal details form and ability to upload a CV, "Our Contact Details" which should also allow for submission of a web enquiry
Should not have
- Aggressive pictures of guards, weapons, etc

```html
<!DOCTYPE html>
<html lang="en">
<head>
<meta charset="utf-8">
<title>Morvane Global Services</title>
<link rel="stylesheet" href="https://fonts.googleapis.com/css2?family=Roboto:wght@400;500;700&family=Roboto+Condensed:wght@400;700&display=swap">
<style>
:root{
  --blue:#0d5aa3;
  --blue-dark:#0a4a88;
  --sky:#2b9ad8;
  --orange:#f7a54a;
  --ink:#2b2b2b;
  --grey-text:#6d6d6d;
  --band:#eeeeee;
  --white:#ffffff;
  --footer:#3b3c3e;
  --panel:rgba(120,120,124,.55);
}
*{box-sizing:border-box;margin:0;padding:0}
html,body{width:1200px;height:2228px;overflow:hidden;background:var(--white)}
body{position:relative;font-family:"Roboto",Arial,sans-serif;color:var(--ink)}
.abs{position:absolute}
.topbar{left:0;top:0;width:1200px;height:33px;background:var(--orange);border-bottom:3px solid var(--blue)}
.join-tab{left:780px;top:0;width:118px;height:33px;background:var(--blue);color:var(--white);font:400 15px "Roboto Condensed",sans-serif;display:flex;align-items:center;justify-content:center}
.follow{left:916px;top:8px;color:var(--blue);font:700 13px "Roboto",sans-serif}
.social{top:4px;width:24px;height:24px;border-radius:50%;background:var(--blue)}
.header{left:0;top:36px;width:1200px;height:86px;background:var(--white)}
.brand{left:98px;top:44px;color:var(--blue);font:700 44px/1 "Roboto",sans-serif;letter-spacing:-1px}
.brand-sub{left:98px;top:94px;width:186px;color:var(--blue);font:700 11px/1 "Roboto",sans-serif;letter-spacing:1.4px;text-align:center}
.nav{top:90px;font:400 15px "Roboto Condensed",sans-serif;color:var(--ink);height:20px;line-height:20px}
.nav.active{color:var(--blue);font-weight:700}
.nav-sep{top:88px;width:1px;height:22px;background:#d0d0d0}
.call-ic{left:935px;top:70px}
.call-label{left:973px;top:66px;color:var(--orange);font:400 13px "Roboto Condensed",sans-serif}
.call-num{left:972px;top:82px;color:var(--blue);font:500 21px "Roboto",sans-serif}
.hero{left:0;top:122px;width:1200px;height:408px;background:linear-gradient(90deg,#2f3335 0%,#474d4f 40%,#5f6567 65%,#575c5e 82%,#2e3234 100%)}
.hero-text{left:100px;top:262px;width:470px;color:var(--white);font:400 23px/34.5px "Roboto Condensed",sans-serif}
.hero-arrow{top:306px;width:38px;height:32px;background:#5b5f61;border:2px solid #888}
.section-title{left:0;width:1200px;text-align:center;font:400 27px "Roboto Condensed",sans-serif;color:var(--ink)}
.section-title span{color:var(--sky)}
.rule{height:1px;background:#c9c9c9}
.rule-mark{height:3px;background:var(--blue)}
.lede{left:0;width:1200px;text-align:center;font:400 12px/19px Arial,sans-serif;color:var(--ink)}
.services{left:0;top:530px;width:1200px;height:368px;background:var(--band)}
.svc-icon{top:656px;width:104px;height:104px}
.svc-name{top:782px;width:180px;text-align:center;font:400 15px "Roboto Condensed",sans-serif;color:var(--ink)}
.svc-desc{top:812px;width:160px;text-align:center;font:400 12px/15.5px Arial,sans-serif;color:var(--grey-text)}
.read-more{left:0;top:1066px;width:1200px;text-align:center;font:400 12px Arial,sans-serif;color:var(--blue);text-decoration:underline}
.divider{left:150px;top:1114px;width:900px;height:6px;background:radial-gradient(ellipse at center,rgba(0,0,0,.12) 0%,rgba(0,0,0,0) 70%)}
.map-frame{left:108px;top:1255px;width:482px;height:226px;border:3px solid #f4c48d;background:var(--white);padding:6px}
.map-fill{width:100%;height:100%;background:linear-gradient(90deg,#2fc12f 0%,#1e8f1e 25%,#f3d03a 45%,#e86a1a 65%,#d1447e 100%);opacity:.85}
.country{font:400 13px Arial,sans-serif;color:var(--ink);display:flex;align-items:center;gap:8px;height:20px}
.why{left:0;top:1515px;width:1200px;height:345px;background:var(--band)}
.why-item{left:0;width:1200px;display:flex;justify-content:center;align-items:center;gap:8px;font:400 12px Arial,sans-serif;color:var(--ink)}
.footer{left:0;top:1860px;width:1200px;height:330px;background:var(--footer)}
.footer-map{left:0;top:1860px;width:1200px;height:330px;background:linear-gradient(135deg,#3a3b3d,#47484a 50%,#3a3b3d)}
.f-heading{left:129px;top:1880px;color:var(--white);font:400 18px "Roboto Condensed",sans-serif}
.f-rule{left:129px;top:1906px;width:150px;height:1px;background:#777}
.f-item{left:134px;color:var(--white);font:400 13px/19px Arial,sans-serif}
.f-icon{left:100px}
.f-brand{left:440px;top:1970px;width:370px;text-align:center;color:var(--white);font:700 68px/1 "Roboto",sans-serif;letter-spacing:-1px}
.f-brand-sub{left:440px;top:2048px;width:370px;text-align:center;color:var(--white);font:400 16px "Roboto",sans-serif;letter-spacing:2.4px}
.inquiry{left:809px;top:1879px;width:287px;height:297px;background:var(--panel);border-top:2px solid #ddd}
.inq-title{left:868px;top:1900px;color:var(--white);font:400 22px "Roboto Condensed",sans-serif}
.inq-sub{left:821px;top:1948px;color:var(--white);font:400 11px Arial,sans-serif}
.field{left:821px;width:262px;height:30px;background:rgba(255,255,255,.12);border-bottom:1px solid rgba(255,255,255,.3);color:#ddd;font:400 11px Arial,sans-serif;padding:8px 12px}
.submit{left:821px;top:2130px;width:110px;height:28px;background:var(--orange);color:var(--blue-dark);font:700 15px "Roboto",sans-serif;display:flex;align-items:center;justify-content:center;border:1px solid #e88a20}
.copyright{left:0;top:2190px;width:1200px;height:38px;background:var(--orange);color:var(--white);font:400 11px Arial,sans-serif;display:flex;align-items:center;justify-content:center}
</style>
</head>
<body>

<div class="abs topbar"></div>
<div class="abs join-tab">Join Our Team</div>
<div class="abs follow">Follow Us On</div>
<div class="abs social" style="left:1001px"></div>
<div class="abs social" style="left:1035px"></div>
<div class="abs social" style="left:1069px"></div>

<header class="abs header"></header>
<div class="abs brand">Morvane</div>
<div class="abs brand-sub">GLOBAL SERVICES</div>

<nav>
  <div class="abs nav active" style="left:389px">Home</div>
  <div class="abs nav-sep" style="left:443px"></div>
  <div class="abs nav" style="left:460px">About Us</div>
  <div class="abs nav-sep" style="left:536px"></div>
  <div class="abs nav" style="left:554px">Services</div>
  <div class="abs nav-sep" style="left:624px"></div>
  <div class="abs nav" style="left:641px">Our Expertise</div>
  <div class="abs nav-sep" style="left:748px"></div>
  <div class="abs nav" style="left:765px">Clients</div>
  <div class="abs nav-sep" style="left:825px"></div>
  <div class="abs nav" style="left:842px">Contact Us</div>
</nav>

<svg class="abs call-ic" width="32" height="32" viewBox="0 0 32 32"><circle cx="16" cy="16" r="14" fill="none" stroke="var(--orange)" stroke-width="2"/><path d="M11 9c2 0 3 3 2 4l-1 1c1 2 3 4 5 5l1-1c1-1 4 0 4 2s-2 3-4 2c-4-1-8-5-9-9-1-2 0-4 2-4z" fill="var(--orange)"/></svg>
<div class="abs call-label">Call Us Today</div>
<div class="abs call-num">123-456-7890</div>

<section class="abs hero" role="img" aria-label="Photo of a consultant drawing a risk management diagram on a glass screen"></section>
<div class="abs hero-text">We Provide Security Services of Various Types In Challenging or High Threat Environments Internationally For Government &amp; Private Sector Organizations.</div>
<div class="abs hero-arrow" style="left:0"><svg width="34" height="28" viewBox="0 0 34 28"><path d="M20 8l-6 6 6 6" fill="none" stroke="#fff" stroke-width="3"/></svg></div>
<div class="abs hero-arrow" style="left:1160px"><svg width="34" height="28" viewBox="0 0 34 28"><path d="M14 8l6 6-6 6" fill="none" stroke="#fff" stroke-width="3"/></svg></div>

<section class="abs services"></section>
<h2 class="abs section-title" style="top:564px"><span>Services</span> We Provide</h2>
<p class="abs lede" style="top:598px">Lorem ipsum dolor sit amet, consectetur adipiscing elit. Aenean et dignissim sem,&nbsp; interdum risus. Vestibulum consectetur</p>
<div class="abs rule" style="left:276px;top:622px;width:648px"></div>
<div class="abs rule-mark" style="left:578px;top:620px;width:66px"></div>

<svg class="abs svc-icon" style="left:117px" viewBox="0 0 104 104"><circle cx="52" cy="52" r="50" fill="#fff" stroke="var(--blue)" stroke-width="3"/><circle cx="52" cy="52" r="44" fill="var(--orange)"/><path d="M34 62l22-22 8 8-22 22z M34 70h10" stroke="#fff" stroke-width="4" fill="none"/><path d="M60 64l8 14h-16z" fill="none" stroke="#fff" stroke-width="3"/></svg>
<svg class="abs svc-icon" style="left:294px" viewBox="0 0 104 104"><circle cx="52" cy="52" r="50" fill="#fff" stroke="var(--blue)" stroke-width="3"/><circle cx="52" cy="52" r="44" fill="var(--blue)"/><rect x="44" y="30" width="26" height="18" fill="#fff"/><circle cx="38" cy="44" r="5" fill="#fff"/><circle cx="40" cy="64" r="5" fill="#fff"/><circle cx="52" cy="64" r="5" fill="#fff"/><circle cx="64" cy="64" r="5" fill="#fff"/><rect x="34" y="70" width="36" height="6" fill="#fff"/></svg>
<svg class="abs svc-icon" style="left:471px" viewBox="0 0 104 104"><circle cx="52" cy="52" r="50" fill="#fff" stroke="var(--blue)" stroke-width="3"/><circle cx="52" cy="52" r="44" fill="var(--blue)"/><circle cx="54" cy="42" r="12" fill="#fff"/><path d="M49 42h10M54 37v10" stroke="var(--blue)" stroke-width="3"/><path d="M28 62c8 0 14 2 18 4h16c4 0 4 6 0 6H48l22-2 8-8" fill="none" stroke="#fff" stroke-width="3"/></svg>
<svg class="abs svc-icon" style="left:641px" viewBox="0 0 104 104"><circle cx="52" cy="52" r="50" fill="#fff" stroke="var(--blue)" stroke-width="3"/><circle cx="52" cy="52" r="44" fill="var(--blue)"/><path d="M52 26l20 8v14c0 14-10 24-20 28-10-4-20-14-20-28V34z" fill="#fff"/><circle cx="52" cy="46" r="6" fill="var(--blue)"/><path d="M42 62c2-6 18-6 20 0z" fill="var(--blue)"/></svg>
<svg class="abs svc-icon" style="left:811px" viewBox="0 0 104 104"><circle cx="52" cy="52" r="50" fill="#fff" stroke="var(--blue)" stroke-width="3"/><circle cx="52" cy="52" r="44" fill="var(--blue)"/><path d="M30 46h10l22-12v36L40 58H30z" fill="#fff"/><path d="M68 44c4 4 4 12 0 16M72 38c8 6 8 22 0 28" stroke="#fff" stroke-width="3" fill="none"/></svg>
<svg class="abs svc-icon" style="left:976px" viewBox="0 0 104 104"><circle cx="52" cy="52" r="50" fill="#fff" stroke="var(--blue)" stroke-width="3"/><circle cx="52" cy="52" r="44" fill="var(--blue)"/><circle cx="44" cy="50" r="5" fill="#fff"/><circle cx="60" cy="50" r="5" fill="#fff"/><rect x="38" y="57" width="28" height="12" fill="#fff"/><path d="M30 30l8 8M74 30l-8 8M30 76l8-8M74 76l-8-8" stroke="#fff" stroke-width="3"/></svg>

<div class="abs svc-name" style="left:79px">Risk Assessments</div>
<div class="abs svc-name" style="left:256px">Security Audits And Training</div>
<div class="abs svc-name" style="left:433px">Medical Support</div>
<div class="abs svc-name" style="left:603px">Protection For Individuals</div>
<div class="abs svc-name" style="left:773px">Crisis Management</div>
<div class="abs svc-name" style="left:938px">Evacuation Coordination</div>
<p class="abs svc-desc" style="left:89px">Lorem ipsum dolr sit amet, consectetur adipiscing elit. Aenean et dign.</p>
<p class="abs svc-desc" style="left:266px">Lorem ipsum dolr sit amet, consectetur adipiscing elit. Aenean et dign.</p>
<p class="abs svc-desc" style="left:443px">Lorem ipsum dolr sit amet, consectetur adipiscing elit. Aenean et dign.</p>
<p class="abs svc-desc" style="left:613px">Lorem ipsum dolr sit amet, consectetur adipiscing elit. Aenean et dign.</p>
<p class="abs svc-desc" style="left:783px">Lorem ipsum dolr sit amet, consectetur adipiscing elit. Aenean et dign.</p>
<p class="abs svc-desc" style="left:948px">Lorem ipsum dolr sit amet, consectetur adipiscing elit. Aenean et dign.</p>

<h2 class="abs section-title" style="top:926px"><span>Welcome to Morvane</span> Global Services</h2>
<div class="abs rule" style="left:294px;top:972px;width:612px"></div>
<div class="abs rule-mark" style="left:567px;top:970px;width:66px"></div>
<p class="abs lede" style="top:986px;left:156px;width:888px">Lorem ipsum dolor sit amet, consectetuer adipiscing elit, sed diam nonummy nibh euismod tincidunt ut laoreet dolore magna aliquam erat volutpat. Ut wisi enim ad minim veniam, quis nostrud exerci tation ullamcorper suscipit lobortis nisl ut aliquip ex ea commodo consequat. Duis autem vel eum iriure dolor in hendrerit in vulputate velit esse molestie consequat, vel illum dolore eu feugiat nulla facilisis at vero eros et accumsan et iusto odio dignissim qui blandit praesent luptatum zzril delenit augue duis dolore te feugait nulla facilisi.</p>
<div class="abs read-more">Read more</div>
<div class="abs divider"></div>

<h2 class="abs section-title" style="top:1148px"><span>We Have</span> Experience Operating In</h2>
<div class="abs rule" style="left:309px;top:1194px;width:582px"></div>
<div class="abs rule-mark" style="left:567px;top:1192px;width:66px"></div>
<p class="abs lede" style="top:1209px;left:170px;width:860px">Lorem ipsum dolor situ scipit lobortis nisl ut aliquip ex ea commodo consequat.&nbsp; amet, consectetuer adipiscing elit, sed diam nonummy nibh euismo&nbsp; dolore suscipit lobortis nisl ut aliquip ex ea commodo consequat.</p>

<div class="abs map-frame"><div class="map-fill" role="img" aria-label="World map with the regions of operation coloured in"></div></div>

<svg width="0" height="0" style="position:absolute"><symbol id="tick" viewBox="0 0 12 12"><circle cx="6" cy="6" r="5" fill="none" stroke="var(--blue)" stroke-width="1.3"/><path d="M3.5 6l2 2 4-4.5" fill="none" stroke="var(--blue)" stroke-width="1.6"/></symbol></svg>

<div class="abs" style="left:612px;top:1287px">
  <div class="country"><svg width="12" height="12"><use href="#tick"/></svg>USA</div>
  <div class="country" style="margin-top:8px"><svg width="12" height="12"><use href="#tick"/></svg>Canada</div>
  <div class="country" style="margin-top:8px"><svg width="12" height="12"><use href="#tick"/></svg>UK</div>
  <div class="country" style="margin-top:8px"><svg width="12" height="12"><use href="#tick"/></svg>France</div>
  <div class="country" style="margin-top:8px"><svg width="12" height="12"><use href="#tick"/></svg>Bosnia</div>
  <div class="country" style="margin-top:8px"><svg width="12" height="12"><use href="#tick"/></svg>UAE</div>
</div>
<div class="abs" style="left:767px;top:1285px">
  <div class="country"><svg width="12" height="12"><use href="#tick"/></svg>Qatar</div>
  <div class="country" style="margin-top:8px"><svg width="12" height="12"><use href="#tick"/></svg>Libya</div>
  <div class="country" style="margin-top:8px"><svg width="12" height="12"><use href="#tick"/></svg>Tunisia</div>
  <div class="country" style="margin-top:8px"><svg width="12" height="12"><use href="#tick"/></svg>Afghanistan</div>
  <div class="country" style="margin-top:8px"><svg width="12" height="12"><use href="#tick"/></svg>Iraq</div>
  <div class="country" style="margin-top:8px"><svg width="12" height="12"><use href="#tick"/></svg>Turkey</div>
</div>
<div class="abs" style="left:942px;top:1288px">
  <div class="country"><svg width="12" height="12"><use href="#tick"/></svg>Sudan</div>
  <div class="country" style="margin-top:8px"><svg width="12" height="12"><use href="#tick"/></svg>Egypt</div>
  <div class="country" style="margin-top:8px"><svg width="12" height="12"><use href="#tick"/></svg>Central African Republic</div>
  <div class="country" style="margin-top:8px"><svg width="12" height="12"><use href="#tick"/></svg>Somalia</div>
  <div class="country" style="margin-top:8px"><svg width="12" height="12"><use href="#tick"/></svg>Rwanda</div>
  <div class="country" style="margin-top:8px"><svg width="12" height="12"><use href="#tick"/></svg>Somaliland</div>
</div>

<section class="abs why"></section>
<h2 class="abs section-title" style="top:1556px"><span>Why</span> Choose Us</h2>
<div class="abs rule" style="left:309px;top:1603px;width:582px"></div>
<div class="abs rule-mark" style="left:567px;top:1601px;width:66px"></div>
<p class="abs lede" style="top:1626px;left:320px;width:560px">Lorem ipsum dolor sit amet, consectetuer adipiscing elit, sed diam nonummy nibh euismo&nbsp; dolore suscipit lobortis nisl ut aliquip ex ea commodo consequat.</p>
<div class="abs why-item" style="top:1677px"><svg width="12" height="12"><use href="#tick"/></svg>Lorem ipsum dolor sit amet, consectetuer adipiscing elit, sed diam nonummy Lorem ipsum dolor sit ameta</div>
<div class="abs why-item" style="top:1707px"><svg width="12" height="12"><use href="#tick"/></svg>Lorem ipsum dolor sit amet, consectetuer adipiscing elit, sed diam nonummy Lorem ipsum</div>
<div class="abs why-item" style="top:1737px"><svg width="12" height="12"><use href="#tick"/></svg>Lorem ipsum dolor sit amet, consectetuer adipiscing elit, sed diam nonummy Lorem ipsum dolor</div>
<div class="abs why-item" style="top:1767px"><svg width="12" height="12"><use href="#tick"/></svg>Lorem ipsum dolor sit amet, consectetuer adipiscing elit, sed diam nonummy Lorem ipsum dolor sit</div>
<div class="abs why-item" style="top:1797px"><svg width="12" height="12"><use href="#tick"/></svg>Lorem ipsum dolor sit amet, consectetuer adipiscing elit, sed diam nonummy</div>

<footer class="abs footer"></footer>
<div class="abs footer-map" role="img" aria-label="Dark street map of the office area"></div>
<h3 class="abs f-heading">Contact Information</h3>
<div class="abs f-rule"></div>

<svg class="abs f-icon" style="top:1926px" width="16" height="20" viewBox="0 0 16 20"><path d="M8 1a6 6 0 0 1 6 6c0 5-6 12-6 12S2 12 2 7a6 6 0 0 1 6-6z" fill="#fff"/><circle cx="8" cy="7" r="2.4" fill="var(--footer)"/></svg>
<div class="abs f-item" style="top:1924px">Postal Address<br>Street Name, City Name State Zipcode</div>
<svg class="abs f-icon" style="top:1976px" width="18" height="18" viewBox="0 0 18 18"><path d="M4 1c2 0 3 4 2 5l-1 1c1 2 3 4 5 5l1-1c1-1 5 0 5 2s-2 4-4 3C7 15 3 11 1 6 0 4 2 1 4 1z" fill="#fff"/></svg>
<div class="abs f-item" style="top:1975px">Telephone<br>123-456-7890&nbsp; &amp;&nbsp; Fax: 456-789-4560</div>
<svg class="abs f-icon" style="top:2028px" width="16" height="12" viewBox="0 0 16 12"><rect width="16" height="12" fill="#fff"/><path d="M0 0l8 6 8-6" fill="none" stroke="var(--footer)" stroke-width="1.5"/></svg>
<div class="abs f-item" style="top:2025px">Email<br>Information: inquiry@morvanegs.example</div>
<svg class="abs f-icon" style="top:2079px" width="14" height="14" viewBox="0 0 14 14"><circle cx="7" cy="7" r="6" fill="#fff"/></svg>
<div class="abs f-item" style="top:2076px">Social Page<br>social.example/MorvaneGS</div>
<svg class="abs f-icon" style="top:2129px" width="14" height="14" viewBox="0 0 14 14"><rect width="13" height="13" fill="#fff"/></svg>
<div class="abs f-item" style="top:2126px">Network Page<br>network.example/MorvaneGS</div>

<div class="abs f-brand">Morvane</div>
<div class="abs f-brand-sub">GLOBAL SERVICES</div>

<aside class="abs inquiry"></aside>
<svg class="abs" style="left:825px;top:1898px" width="34" height="34" viewBox="0 0 34 34"><circle cx="17" cy="17" r="16" fill="#fff"/><path d="M12 9c2 0 3 3 2 4l-1 1c1 2 3 4 5 5l1-1c1-1 4 0 4 2s-2 3-4 2c-4-1-8-5-9-9-1-2 0-4 2-4z" fill="var(--orange)"/></svg>
<div class="abs inq-title">Quick Inquiry</div>
<div class="abs inq-sub">Lorem ipsum dolor sit amet, consectetuer</div>
<div class="abs field" style="top:1973px">Name</div>
<div class="abs field" style="top:2007px">Email</div>
<div class="abs field" style="top:2041px">Phone</div>
<div class="abs field" style="top:2075px;height:40px">Message</div>
<div class="abs submit">SUBMIT</div>

<div class="abs copyright">© 2015&nbsp; MorvaneGlobalServices&nbsp; All rights reserved</div>

</body>
</html>
```